Set up small scale company website

We need a website set up for our educational consultancy - Vexmore Education. We like the following site and want something similar www.plindarhub.co.uk We can provide the copy and images but need the following:- setting up the overall theme and design - to our requirements on colours and forma- Approximately 4 pages of services offered and with an index pageEtct (yellow and green)And the following pages - as well as a home page:- A contact page linked to our email addresses and registered business address 17 Wexbury Lane, Harwich, Essex, CO14 8PN- About Us page - An index of services page that links to between 4-6 pages outlining services- A News page that links to updates of latest services, events and activities - easily updated by usOn the homepage we'd like links to chirpnet and WorkLoop feeds and links to our other blogs and websites
Target Market(s)
Schools, local authoroties and multi-academy trusts
Logo Text
Vexmore Education
Coding
Coded - Design and coding required
Number of Pages Required
5+ page
Font styles to use
Requirements
Should not have
- No tacky pictures of mortar boards or chalk boards etc.

```html
<!DOCTYPE html>
<html lang="en">
<head>
<meta charset="utf-8">
<title>Vexmore Education</title>
<link href="https://fonts.googleapis.com/css2?family=Lato:wght@400;700;900&family=Arimo:wght@400;700&display=swap" rel="stylesheet">
<style>
:root{
  --green:#9bcb2a;
  --green-dark:#86b81f;
  --yellow:#f6e51a;
  --ink:#2e2e2e;
  --text:#555;
  --muted:#9a9a9a;
  --white:#fff;
}
*{box-sizing:border-box;margin:0;padding:0}
html,body{width:1200px;height:3203px;overflow:hidden;background:var(--white)}
body{font-family:"Arimo",Arial,sans-serif;color:var(--text)}
.page{position:relative;width:1200px;height:3203px;overflow:hidden}
.abs{position:absolute}
/* header */
.logo{left:77px;top:36px;font:700 52px/1 "Lato",sans-serif;color:var(--ink);letter-spacing:-0.5px}
.phone-tab{left:886px;top:0;width:256px;height:47px;background:var(--green);border-radius:0 0 10px 30px;color:var(--white);font:700 22px/47px "Arimo",sans-serif;text-align:center}
.phone-tab svg{vertical-align:-3px;margin-right:10px}
.nav{right:58px;top:74px;display:flex;gap:14px;align-items:center}
.nav a{font:700 14px/1 "Arimo",sans-serif;color:var(--ink);text-decoration:none;padding:8px 12px;border-radius:16px}
.nav a.active{background:var(--green);color:var(--white);padding:8px 18px}
/* hero */
.hero{left:0;top:117px;width:1200px;height:580px;background:linear-gradient(135deg,#4a5a66 0%,#8a7f74 35%,#c9b9a6 55%,#6b6f70 80%,#2f3438 100%)}
.hero-wave{left:0;top:600px}
.hero-title{left:0;top:318px;width:1200px;text-align:center;font:900 86px/1 "Lato",sans-serif;color:var(--white)}
.hero-sub{left:0;top:409px;width:1200px;text-align:center;font:700 28px/1.25 "Lato",sans-serif;color:var(--white)}
.dots{left:567px;top:592px;display:flex;gap:8px}
.dots span{width:14px;height:14px;border-radius:50%;background:var(--white)}
.dots span:first-child{background:var(--green)}
/* welcome */
.section-title{font:700 25px/1 "Arimo",sans-serif;color:var(--ink)}
.welcome-title{left:77px;top:752px}
.para{font:400 15px/24px "Arimo",sans-serif;color:var(--text)}
.welcome-text{left:77px;top:797px;width:600px}
.welcome-text p+p{margin-top:12px}
.btn{display:block;background:var(--yellow);color:var(--ink);font:700 16px/52px "Arimo",sans-serif;text-align:center;border-radius:26px;text-decoration:none}
.welcome-btn{left:75px;top:1007px;width:164px}
.welcome-photo{left:705px;top:747px;width:420px;height:314px;border-radius:6px;background:linear-gradient(160deg,#e9e6df,#c8cdd0 50%,#7f8b96)}
/* services */
.services-band{left:0;top:1114px}
.card{width:222px;height:205px;background:var(--white);border-radius:34px;transform:skewX(-7deg);text-align:center}
.card-inner{transform:skewX(7deg);padding-top:28px}
.card h3{font:700 20px/1 "Arimo",sans-serif;color:var(--ink);margin:14px 0 12px}
.card p{font:400 14px/21px "Arimo",sans-serif;color:var(--text);width:160px;margin:0 auto}
.c1{left:82px;top:1196px}.c2{left:348px;top:1196px}.c3{left:82px;top:1441px}.c4{left:348px;top:1441px}
.services-title{left:677px;top:1296px;color:var(--white)}
.services-text{left:677px;top:1340px;width:420px;color:var(--white)}
.services-btn{left:677px;top:1494px;width:164px}
/* news */
.news-title{left:0;top:1784px;width:1200px;text-align:center}
.news-card{width:331px}
.news-photo{width:331px;height:192px;border-radius:6px}
.date{left:10px;top:-15px;width:81px;height:86px;background:var(--green);border-radius:0 0 8px 30px;color:var(--white);text-align:center;font-family:"Arimo",sans-serif;padding-top:6px}
.date b{display:block;font-size:17px;line-height:1}
.date strong{display:block;font-size:38px;line-height:36px}
.date small{display:block;font-size:15px;font-weight:700;line-height:1}
.news-card h4{font:700 17px/1 "Arimo",sans-serif;color:var(--green);margin:26px 0 10px}
.news-card p{font:400 15px/26px "Arimo",sans-serif;color:var(--text)}
.n1{left:75px;top:1868px}.n2{left:433px;top:1868px}.n3{left:794px;top:1868px}
.p1{background:linear-gradient(135deg,#8d7465,#c8b9ad 50%,#55606a)}
.p2{background:linear-gradient(135deg,#3e4b52,#8a8f8c 50%,#27323a)}
.p3{background:linear-gradient(135deg,#c59a7c,#e6d6c6 50%,#b97a5a)}
/* feeds */
.feeds-band{left:0;top:2252px}
.feeds-title{top:2350px;font:700 25px/1 "Arimo",sans-serif;color:var(--white);text-align:center;width:330px}
.feed-box{top:2404px;width:329px;height:389px;background:var(--white);border-radius:8px;padding:36px 16px 0 16px}
.feed-item{display:flex;gap:16px;height:115px}
.feed-logo{flex:0 0 80px;height:58px;margin-top:12px;border:1px solid #ddd;font:700 10px/13px "Arimo",sans-serif;color:#555;text-align:center;padding-top:16px}
.feed-item h5{font:400 17px/1 "Arimo",sans-serif;color:var(--green);margin-bottom:6px}
.feed-item p{font:400 14px/21px "Arimo",sans-serif;color:var(--ink)}
/* footer */
.foot-logo{left:75px;top:2964px;font:700 38px/34px "Lato",sans-serif;color:var(--muted)}
.foot-copy{left:75px;top:3049px;font:400 12px/17px "Arimo",sans-serif;color:var(--ink)}
.social{left:75px;top:3102px;display:flex;gap:18px}
.social span{width:16px;height:16px;border-radius:50%;background:var(--ink)}
.foot-head{font:700 12px/1 "Arimo",sans-serif;color:var(--green)}
.foot-list{list-style:none;font:400 13px/28px "Arimo",sans-serif;color:var(--ink)}
.foot-contact{font:400 13px/18px "Arimo",sans-serif;color:var(--ink)}
.foot-contact li{list-style:none;display:flex;gap:18px;margin-top:9px;align-items:center}
.input{width:207px;height:37px;border:1px solid #aaa;border-radius:19px;font:400 13px/35px "Arimo",sans-serif;color:var(--ink);padding-left:20px}
.signup{left:1038px;top:3077px;width:88px;height:36px;background:var(--green);color:var(--white);border-radius:18px;font:700 13px/36px "Arimo",sans-serif;text-align:center}
</style>
</head>
<body>
<div class="page">

<header>
  <div class="abs logo">VEXMORE EDUCATION</div>
  <div class="abs phone-tab"><svg width="18" height="18" viewBox="0 0 24 24"><path fill="#fff" d="M6.6 10.8a15 15 0 0 0 6.6 6.6l2.2-2.2c.3-.3.7-.4 1-.2 1.1.4 2.3.6 3.6.6.6 0 1 .4 1 1V20c0 .6-.4 1-1 1A17 17 0 0 1 3 4c0-.6.4-1 1-1h3.5c.6 0 1 .4 1 1 0 1.3.2 2.5.6 3.6.1.3 0 .7-.2 1z"/></svg>1-800-555-0147</div>
  <nav class="abs nav">
    <a class="active" href="#">HOME</a><a href="#">SERVICES</a><a href="#">NEWS</a><a href="#">ABOUT US</a><a href="#">CONTACT US</a>
  </nav>
</header>

<section>
  <div class="abs hero" role="img" aria-label="Photo of a consultant guiding two young men working at computers"></div>
  <svg class="abs hero-wave" width="1200" height="100" viewBox="0 0 1200 100"><path fill="#fff" d="M0 45 C200 100 380 110 560 75 C760 35 900 40 1200 20 V100 H0Z"/></svg>
  <h1 class="abs hero-title">VEXMORE EDUCATION</h1>
  <p class="abs hero-sub">Donec iaculis nulla ut arcu auctor, fermentum pharetra<br>libero scelerisque.</p>
  <div class="abs dots"><span></span><span></span><span></span></div>
</section>

<section>
  <h2 class="abs section-title welcome-title">WELCOME TO OUR WEBSITE</h2>
  <div class="abs para welcome-text">
    <p>Aenean maximus feugiat purus eget porttitor. Donec iaculis nulla ut arcu auctor, fermentum pharetra libero scelerisque. Morbi posuere dolor nec dapibus cursus. Proin ut nisl ex. Ut convallis, lectus id porttitor blandit, nulla nisi ullamcorper diam, a bibendum justo dolor eu sapien.</p>
    <p>Sed vel urna ligula. Sed sed urna tincidunt erat tincidunt consectetur. Aenean vel efficitur diam, eu iaculis mauris. In hac habitasse platea dictumst. Fusce laoreet blandit lacus, nec tristique nibh pulvinar sit amet.</p>
  </div>
  <a class="abs btn welcome-btn" href="#">READ MORE</a>
  <div class="abs welcome-photo" role="img" aria-label="Photo of a small group seated in a circle in a bright office"></div>
</section>

<section>
  <svg class="abs services-band" width="1200" height="616" viewBox="0 0 1200 616"><polygon fill="#9bcb2a" points="0,0 1200,39 1200,572 0,616"/></svg>
  <div class="abs card c1"><div class="card-inner">
    <svg width="44" height="40" viewBox="0 0 44 40"><g fill="#9bcb2a"><circle cx="22" cy="9" r="7"/><circle cx="8" cy="14" r="5"/><circle cx="36" cy="14" r="5"/><path d="M10 38c0-9 5-15 12-15s12 6 12 15z"/><path d="M0 36c0-7 3-12 8-12 2 0 3 .5 4 1.5C9 28 8 32 8 36z"/><path d="M44 36c0-7-3-12-8-12-2 0-3 .5-4 1.5 3 2.5 4 6.5 4 10.5z"/></g></svg>
    <h3>CRAS NON</h3><p>Dolor eu nisi dignissim pretium vel urna ligula sed urna..</p></div></div>
  <div class="abs card c2"><div class="card-inner">
    <svg width="44" height="40" viewBox="0 0 44 40"><g fill="#9bcb2a"><path d="M15 4h14v6h-3V7h-8v3h-3z"/><rect x="2" y="10" width="40" height="28" rx="4"/></g><g fill="#fff"><rect x="11" y="10" width="3" height="28"/><rect x="30" y="10" width="3" height="28"/></g></svg>
    <h3>CRAS NON</h3><p>Dolor eu nisi dignissim pretium vel urna ligula sed urna..</p></div></div>
  <div class="abs card c3"><div class="card-inner">
    <svg width="44" height="40" viewBox="0 0 44 40"><g fill="#9bcb2a"><ellipse cx="18" cy="14" rx="17" ry="12"/><path d="M6 22l-3 10 11-6z"/><path d="M30 28c8-1 12-5 12-10 0-2-1-4-3-6 0 8-7 14-17 16 2 1 5 1 8 0l8 6-2-6z"/></g></svg>
    <h3>CRAS NON</h3><p>Dolor eu nisi dignissim pretium vel urna ligula sed urna..</p></div></div>
  <div class="abs card c4"><div class="card-inner">
    <svg width="44" height="40" viewBox="0 0 44 40"><g transform="skewX(-12) translate(8 0)"><rect x="6" y="2" width="28" height="34" rx="2" fill="#9bcb2a"/><g fill="#fff"><rect x="12" y="9" width="16" height="3"/><rect x="12" y="16" width="16" height="3"/><rect x="10" y="30" width="24" height="3"/></g></g></svg>
    <h3>CRAS NON</h3><p>Dolor eu nisi dignissim pretium vel urna ligula sed urna..</p></div></div>
  <h2 class="abs section-title services-title" style="color:var(--white)">OUR SERVICES</h2>
  <p class="abs para services-text">Aenean maximus feugiat purus eget porttitor. Donec iaculis nulla ut arcu auctor,  fermentum pharetra libero scelerisque. Morbi posuere dolor nec dapibus cursus.  Proin ut nisl ex. Ut convallis, lectus id porttitor blandit, nulla nisi ullamcorper diam, a bibendum justo dolor eu sapien.</p>
  <a class="abs btn services-btn" href="#">READ MORE</a>
</section>

<section>
  <h2 class="abs section-title news-title">NEWS</h2>
  <article class="abs news-card n1">
    <div class="news-photo p1" role="img" aria-label="Photo of colleagues reviewing papers at a meeting table"></div>
    <div class="abs date"><b>FEB</b><strong>10</strong><small>2019</small></div>
    <h4>QUISQUE ID MAXIMUS NIBH</h4>
    <p>Aenean maximus feugiat purus eget porttitor. Donec iaculis nulla ut arcu auctor,  fermentum pharetra libero scelerisque...</p>
  </article>
  <article class="abs news-card n2">
    <div class="news-photo p2" role="img" aria-label="Photo of a team gathered around a laptop"></div>
    <div class="abs date"><b>FEB</b><strong>10</strong><small>2019</small></div>
    <h4>QUISQUE ID MAXIMUS NIBH</h4>
    <p>Aenean maximus feugiat purus eget porttitor. Donec iaculis nulla ut arcu auctor,  fermentum pharetra libero scelerisque...</p>
  </article>
  <article class="abs news-card n3">
    <div class="news-photo p3" role="img" aria-label="Photo of a student smiling in a classroom"></div>
    <div class="abs date"><b>FEB</b><strong>10</strong><small>2019</small></div>
    <h4>QUISQUE ID MAXIMUS NIBH</h4>
    <p>Aenean maximus feugiat purus eget porttitor. Donec iaculis nulla ut arcu auctor,  fermentum pharetra libero scelerisque...</p>
  </article>
</section>

<section>
  <svg class="abs feeds-band" width="1200" height="645" viewBox="0 0 1200 645" role="img" aria-label="Green faceted background band">
    <defs><linearGradient id="feedsGrad" x1="0" y1="0" x2="1" y2="1"><stop offset="0" stop-color="#a6d43a"/><stop offset=".5" stop-color="#8fc41f"/><stop offset="1" stop-color="#b3db55"/></linearGradient></defs>
    <path fill="url(#feedsGrad)" d="M0 40 C250 90 420 30 650 45 C850 58 1000 70 1200 0 V630 C900 615 500 600 0 585Z"/>
  </svg>
  <h2 class="abs feeds-title" style="left:256px">CHIRPNET FEEDS</h2>
  <h2 class="abs feeds-title" style="left:615px">WORKLOOP FEEDS</h2>
  <div class="abs feed-box" style="left:256px">
    <div class="feed-item"><div class="feed-logo">VEXMORE<br>EDUCATION</div><div><h5>Brightpath Clinic</h5><p>Pellentesque mollis, lorem ac vehicula aliquet, quam arcu commodo...</p></div></div>
    <div class="feed-item"><div class="feed-logo">VEXMORE<br>EDUCATION</div><div><h5>Brightpath Clinic</h5><p>Pellentesque mollis, lorem ac vehicula aliquet, quam arcu commodo...</p></div></div>
    <div class="feed-item"><div class="feed-logo">VEXMORE<br>EDUCATION</div><div><h5>Brightpath Clinic</h5><p>Pellentesque mollis, lorem ac vehicula aliquet, quam arcu commodo...</p></div></div>
  </div>
  <div class="abs feed-box" style="left:615px">
    <div class="feed-item"><div class="feed-logo">VEXMORE<br>EDUCATION</div><div><h5>Brightpath Clinic</h5><p>Pellentesque mollis, lorem ac vehicula aliquet, quam arcu commodo...</p></div></div>
    <div class="feed-item"><div class="feed-logo">VEXMORE<br>EDUCATION</div><div><h5>Brightpath Clinic</h5><p>Pellentesque mollis, lorem ac vehicula aliquet, quam arcu commodo...</p></div></div>
    <div class="feed-item"><div class="feed-logo">VEXMORE<br>EDUCATION</div><div><h5>Brightpath Clinic</h5><p>Pellentesque mollis, lorem ac vehicula aliquet, quam arcu commodo...</p></div></div>
  </div>
</section>

<footer>
  <div class="abs foot-logo">VEXMORE<br>EDUCATION</div>
  <p class="abs foot-copy">Copyright © 2019. Company Name.<br>All Right Reserved</p>
  <div class="abs social"><span></span><span></span><span></span><span></span><span></span></div>

  <div class="abs" style="left:397px;top:2947px">
    <h6 class="foot-head">SITE MAP</h6>
    <ul class="foot-list" style="margin-top:8px"><li>Home</li><li>Services</li><li>News</li><li>About us</li><li>Contact us</li></ul>
  </div>

  <div class="abs" style="left:630px;top:2947px">
    <h6 class="foot-head">CONTACT INFO</h6>
    <p class="foot-contact" style="margin-top:12px">Mr. Alan Reddle,<br>17 Wexbury Lane, Harwich,<br>Essex, CO14 8PN</p>
    <ul class="foot-contact">
      <li><svg width="12" height="12" viewBox="0 0 24 24"><path fill="#2e2e2e" d="M6.6 10.8a15 15 0 0 0 6.6 6.6l2.2-2.2c.3-.3.7-.4 1-.2 1.1.4 2.3.6 3.6.6.6 0 1 .4 1 1V20c0 .6-.4 1-1 1A17 17 0 0 1 3 4c0-.6.4-1 1-1h3.5c.6 0 1 .4 1 1 0 1.3.2 2.5.6 3.6.1.3 0 .7-.2 1z"/></svg>1-800-555-0147</li>
      <li><svg width="12" height="10" viewBox="0 0 24 18"><path fill="#2e2e2e" d="M0 0h24v18H0z"/><path fill="none" stroke="#fff" stroke-width="2" d="M1 1l11 9 11-9"/></svg>hello@vexmoremail.com</li>
      <li><svg width="12" height="14" viewBox="0 0 24 30"><path fill="#2e2e2e" d="M12 0a10 10 0 0 0-10 10c0 8 10 20 10 20s10-12 10-20A10 10 0 0 0 12 0zm0 14a4 4 0 1 1 0-8 4 4 0 0 1 0 8z"/></svg>Map Location</li>
    </ul>
  </div>

  <h6 class="abs foot-head" style="left:918px;top:2947px">EMAIL SIGN UP</h6>
  <div class="abs input" style="left:918px;top:2983px">Enter Name</div>
  <div class="abs input" style="left:918px;top:3028px">Enter Email Address</div>
  <div class="abs signup">SIGN UP</div>
</footer>

</div>
</body>
</html>
```